NEW Modern Sleek Business Card for VR Language Startup

Our startup is using VR to lead the next wave of world language education. We need a two-sided business card that introduces the larger organization (Brightloom Language Inc) and our contact info on one side and shows the product, Glimwoorld, on the other side.

Side 1 (contact info)= Brightloom Logo and Contact info (name, title, phone, email)

Side 2 (product)= Glimworld logo, text, and website
Text= Culturally Immersive Language Learning Games
Website= www.glimworld-play.com

Target Market(s)

Education, Technology

Contact Information for Business Card

Contact info will be updated upon approval of the design. For now, put this as a placeholder.

Perry Dunmore
Founder & CEO
pdunmore@quillpost-mail.net
(555)-014-2286

Font styles to use
Other font styles liked:
• Gibson and Century Gothic are the brand fonts

Requirements
Nice to have
• I would love to see cohesion between the design and colors of the two logos. I have attached a few business card designs that I like, so you can get a feel for my preferred style.

```html
<!DOCTYPE html>
<html lang="en">
<head>
<meta charset="UTF-8">
<title>Brightloom Language – Business Card</title>
<link rel="stylesheet" href="https://fonts.googleapis.com/css2?family=Questrial&family=Montserrat:wght@500;600&display=swap">
<style>
  :root {
    --stage: #2a2a2a;
    --card-dark: #1f1f1f;
    --card-light: #ffffff;
    --ink-light: #f2f2f2;
    --ink-dark: #1c1c1c;
    --accent-cyan: #2cb8e4;
    --accent-violet: #8a5bb8;
    --accent-orange: #f26a4b;
    --accent-pink: #e84a6f;
  }
  * { box-sizing: border-box; margin: 0; padding: 0; }
  html, body { width: 1200px; height: 900px; overflow: hidden; }
  body {
    background: var(--stage);
    font-family: "Questrial", "Century Gothic", sans-serif;
    display: flex;
    flex-direction: column;
    align-items: center;
    justify-content: center;
    gap: 44px;
  }
  .card {
    position: relative;
    width: 700px;
    height: 400px;
    box-shadow: 0 14px 32px rgba(0,0,0,0.45);
  }
  .card--product { background: var(--card-dark); color: var(--ink-light); }
  .card--contact { background: var(--card-light); color: var(--ink-dark); }

  .brand {
    display: flex;
    align-items: center;
    gap: 16px;
  }
  .brand__dot {
    width: 54px; height: 54px;
    border-radius: 50%;
    flex: none;
    background: linear-gradient(135deg, var(--accent-orange), var(--accent-pink) 45%, var(--accent-violet) 70%, var(--accent-cyan));
  }
  .brand__name {
    font-family: "Montserrat", "Century Gothic", sans-serif;
    font-weight: 600;
    font-size: 40px;
    letter-spacing: 4px;
    text-transform: uppercase;
    white-space: nowrap;
  }
  .card--product .brand {
    position: absolute;
    top: 104px; left: 50%;
    transform: translateX(-50%);
  }
  .card--product .brand__name { color: var(--ink-light); }

  .product__web {
    position: absolute;
    top: 226px; left: 0; right: 0;
    font-size: 19px;
    display: flex; justify-content: center; align-items: center; gap: 10px;
  }
  .product__tagline {
    position: absolute;
    top: 272px; left: 0; right: 0;
    text-align: center;
    font-size: 23px;
  }

  .card--contact .brand {
    position: absolute;
    top: 92px; left: 60px;
  }
  .card--contact .brand__dot { width: 48px; height: 48px; }
  .card--contact .brand__name { font-size: 34px; color: var(--ink-dark); }

  .person {
    position: absolute;
    right: 60px; top: 176px;
    text-align: right;
  }
  .person__name {
    font-family: "Montserrat", "Century Gothic", sans-serif;
    font-weight: 600;
    font-size: 25px;
    color: var(--accent-cyan);
    text-transform: uppercase;
    letter-spacing: 0.5px;
  }
  .person__title { font-size: 19px; margin-top: 2px; }

  .divider {
    position: absolute;
    left: 40px; right: 60px; top: 254px;
    height: 2px;
    background: linear-gradient(90deg, var(--accent-cyan), var(--accent-violet) 55%, var(--accent-orange));
  }

  .contact-list {
    position: absolute;
    right: 60px; top: 274px;
    list-style: none;
    text-align: right;
    font-size: 19px;
    line-height: 1.7;
  }
  .contact-list li { display: flex; justify-content: flex-end; align-items: center; gap: 10px; }
  .icon { width: 15px; height: 15px; flex: none; }
</style>
</head>
<body>

  <section class="card card--product" aria-label="Product side">
    <div class="brand">
      <span class="brand__dot"></span>
      <span class="brand__name">Glimworld</span>
    </div>
    <p class="product__web">
      <svg class="icon" viewBox="0 0 16 16" aria-hidden="true">
        <circle cx="8" cy="8" r="7" fill="none" stroke="#2cb8e4" stroke-width="1.6"/>
        <ellipse cx="8" cy="8" rx="3" ry="7" fill="none" stroke="#2cb8e4" stroke-width="1.2"/>
        <line x1="1" y1="8" x2="15" y2="8" stroke="#2cb8e4" stroke-width="1.2"/>
      </svg>
      www.glimworld-play.com
    </p>
    <p class="product__tagline">Culturally Immersive Language Learning Games</p>
  </section>

  <section class="card card--contact" aria-label="Contact side">
    <div class="brand">
      <span class="brand__dot"></span>
      <span class="brand__name">Brightloom</span>
    </div>
    <div class="person">
      <p class="person__name">Perry Dunmore</p>
      <p class="person__title">Founder &amp; CEO</p>
    </div>
    <div class="divider"></div>
    <ul class="contact-list">
      <li>(555)-014-2286
        <svg class="icon" viewBox="0 0 16 16" aria-hidden="true">
          <path d="M3 2h3l1.5 3.5-2 1.2a8 8 0 0 0 3.8 3.8l1.2-2L14 10v3a1 1 0 0 1-1 1A11 11 0 0 1 2 3a1 1 0 0 1 1-1z" fill="#2cb8e4"/>
        </svg>
      </li>
      <li>pdunmore@quillpost-mail.net
        <svg class="icon" viewBox="0 0 16 16" aria-hidden="true">
          <rect x="1" y="3" width="14" height="10" rx="1" fill="#2cb8e4"/>
          <path d="M1.5 3.8 8 9l6.5-5.2" fill="none" stroke="#fff" stroke-width="1.3"/>
        </svg>
      </li>
    </ul>
  </section>

</body>
</html>
```